Bicycle Tour Schedule on a Business Card

Need to develop a 2 side business card that highlights a series of bike tours on 1 side and a series of events on the other side.
This will be inserted into a card wallet that attaches to a cell phone and will be handed out at an expo. The card wallets are black and red so color must coordinate with both. There is a photo of the card wallets attached.

1 side needs to be devoted to Pedal Vista Trek and the others to KQR Venture events on the other. Dates and websites are very important.

Target Market(s)

Cyclists
Predominantly men ages 40+
Educated, Professionals

Industry/Entity Type

Business

Font styles to use
Serif

Requirements
Must have
• Pedal vista treks logo on 1 side and KQR Venture logo on the other side
• dates and websites clearly visible
• Design of both sides must go together.
• Must be portrait not landscape

```html
<!DOCTYPE html>
<html lang="en">
<head>
<meta charset="utf-8">
<title>Pedal Vista Trek and KQR Venture cycling cards</title>
<link rel="stylesheet" href="https://fonts.googleapis.com/css2?family=PT+Sans:ital,wght@0,400;0,700;1,700&display=swap">
<style>
  :root {
    --backdrop: #8e9091;
    --paper: #f2f2f0;
    --tour-blue: #0b4fa3;
    --tour-green: #3fae49;
    --event-red: #b3122b;
    --event-blue: #1d8fcf;
    --ink: #3a3a3a;
    --white: #ffffff;
  }
  * { box-sizing: border-box; margin: 0; padding: 0; }
  html, body {
    width: 1105px;
    height: 1200px;
    overflow: hidden;
    background: var(--backdrop);
    font-family: "PT Sans", Arial, sans-serif;
  }
  .card-pair {
    position: absolute;
    top: 267px;
    left: 113px;
    display: flex;
    gap: 86px;
  }
  .card {
    position: relative;
    width: 398px;
    height: 698px;
    background: var(--paper);
    overflow: hidden;
  }
  .card-wave {
    position: absolute;
    top: 0;
    left: 0;
    width: 398px;
    height: 400px;
  }
  .brand {
    position: absolute;
    display: flex;
    align-items: center;
    gap: 12px;
    color: var(--white);
    font-weight: 700;
    font-size: 30px;
    letter-spacing: 0.5px;
    white-space: nowrap;
  }
  .brand-dot {
    width: 22px;
    height: 22px;
    border-radius: 50%;
    background: var(--white);
  }
  .brand-square {
    width: 22px;
    height: 22px;
    background: var(--white);
  }
  .tour-card .brand { top: 44px; right: 40px; }
  .event-card .brand { top: 96px; left: 34px; }

  .schedule {
    position: absolute;
    right: 41px;
    width: 330px;
    text-align: right;
    color: var(--ink);
  }
  .tour-card .schedule { top: 338px; }
  .event-card .schedule { top: 278px; }
  .schedule-headline {
    font-style: italic;
    font-weight: 700;
    font-size: 19px;
    line-height: 23px;
    margin-bottom: 12px;
  }
  .tour-card .schedule-headline { color: var(--tour-blue); }
  .event-card .schedule-headline { color: var(--event-red); }
  .schedule-item { margin-bottom: 12px; font-size: 18px; line-height: 22px; }
  .schedule-item:last-child { margin-bottom: 0; }
  .item-name { font-weight: 400; }
  .item-date, .item-site { font-weight: 700; }
</style>
</head>
<body>
  <main class="card-pair">
    <section class="card tour-card" aria-label="Pedal Vista Trek tour schedule">
      <svg class="card-wave" viewBox="0 0 398 400" aria-hidden="true">
        <path d="M0,0 H398 V124 C310,120 260,170 200,240 C150,300 80,335 0,328 Z" fill="var(--tour-blue)"/>
        <path d="M398,124 C310,120 260,170 200,240 C150,300 80,335 0,328" fill="none" stroke="var(--tour-green)" stroke-width="5"/>
      </svg>
      <div class="brand"><span class="brand-dot"></span>Pedal Vista Trek</div>
      <div class="schedule">
        <p class="schedule-headline">Fully supported bike tours.<br>Discover the hidden gems on<br>two wheels</p>
        <div class="schedule-item"><p class="item-name">Heart of Colorado</p><p class="item-date">June 26 - July 2, 2016</p></div>
        <div class="schedule-item"><p class="item-name">Colorado Front Range Tour</p><p class="item-date">August 14-20, 2016</p></div>
        <div class="schedule-item"><p class="item-name">Cape Cod Tour</p><p class="item-date">October 9 -15, 2016</p></div>
        <div class="schedule-item"><p class="item-name">Florida Key Tours</p><p class="item-date">November 6-12, 2016 &amp;<br>December 4-10, 2016</p></div>
      </div>
    </section>

    <section class="card event-card" aria-label="KQR Venture event schedule">
      <svg class="card-wave" viewBox="0 0 398 400" aria-hidden="true">
        <path d="M0,0 H398 V142 C330,140 290,160 240,195 C180,240 100,305 0,320 Z" fill="var(--event-red)"/>
        <path d="M398,142 C330,140 290,160 240,195 C180,240 100,305 0,320" fill="none" stroke="var(--event-blue)" stroke-width="5"/>
      </svg>
      <div class="brand"><span class="brand-square"></span>KQR Venture</div>
      <div class="schedule">
        <p class="schedule-headline">Junior Spoke Series:<br>Cycling camps for youth</p>
        <div class="schedule-item"><p class="item-name">Mountain Bike Camp</p><p class="item-date">July 8-10, 2016</p></div>
        <div class="schedule-item"><p class="item-name">Cyclocross Camp</p><p class="item-date">August 26-28, 2016</p><p class="item-site">Juniorspokeseries.org</p></div>
        <div class="schedule-item"><p class="item-name">Mile High Hundred Ride</p><p class="item-date">June 18, 2016</p><p class="item-site">Milehighhundred.com</p></div>
        <div class="schedule-item"><p class="item-name">Colorado Trail 2 Trail Challenge</p><p class="item-date">July 30, 2016 - Cotrail2trail.com</p></div>
        <div class="schedule-item"><p class="item-name">Zany Pedal Ride</p><p class="item-date">September 11, 2016</p><p class="item-site">zanypedalride.com</p></div>
      </div>
    </section>
  </main>
</body>
</html>
```